175th Anniversary of Family Owned Funeral Home Pole Banners

We are family owned and operated funeral home in the Greater Cincinnati area and operate 3 funeral homes and a cremation center and we will be celebrating our 175th anniversary in 2015. The communities we serve look to us as leaders in the community and we are very well recognized. In preparation for next year, part of our planning includes placing pole banners in our local communities and our funeral home parking areas. The banner dimensions will be 30 x 60. We need for the banners to display a great message of tradition and excellence. Our website is www.brannockwelde.com I have uploaded an example of a pole banner as well as our logo(s).
Updates
Original artwork has been uploaded if needed.
Industry/Entity Type
Funeral Home

```html
<!DOCTYPE html>
<html lang="en">
<head>
<meta charset="utf-8">
<title>Brannock Welde – 175th Anniversary Pole Banner</title>
<link rel="stylesheet" href="https://fonts.googleapis.com/css2?family=Lora:ital,wght@0,400;1,400&display=swap">
<style>
  :root {
    --page: #ffffff;
    --banner: #2e3f7c;
    --banner-soft: #3b4d8c;
    --ink: #ffffff;
  }
  html, body {
    margin: 0;
    padding: 0;
    width: 1200px;
    height: 1000px;
    overflow: hidden;
    background: var(--page);
  }
  .canvas {
    position: relative;
    width: 1200px;
    height: 1000px;
  }
  .banner {
    position: absolute;
    left: 369px;
    top: 37px;
    width: 465px;
    height: 929px;
    background: var(--banner);
    box-shadow: 0 6px 18px rgba(0, 0, 0, 0.18);
    color: var(--ink);
    font-family: "Lora", Georgia, serif;
  }
  .banner-frame {
    position: absolute;
    inset: 0;
  }
  .text-line {
    position: absolute;
    left: 0;
    width: 100%;
    margin: 0;
    text-align: center;
    font-style: italic;
    font-weight: 400;
    line-height: 1;
  }
  .intro { top: 26px; font-size: 44px; }
  .milestone-ornament {
    position: absolute;
    left: 90px;
    top: 80px;
    width: 285px;
    height: 218px;
  }
  .milestone-number {
    position: absolute;
    left: 0;
    width: 100%;
    top: 132px;
    text-align: center;
    font-size: 68px;
    line-height: 1;
    margin: 0;
  }
  .milestone-unit { top: 196px; font-size: 28px; }
  .occasion { top: 292px; font-size: 50px; }
  .brand-mark {
    position: absolute;
    left: 142px;
    top: 410px;
    width: 180px;
    height: 180px;
    border-radius: 50%;
    background: var(--ink);
  }
  .brand-name { top: 740px; font-size: 46px; }
  .divider {
    position: absolute;
    left: 34px;
    right: 34px;
    top: 810px;
    height: 2px;
    background: var(--ink);
  }
  .service { font-size: 28px; }
  .service-homes { top: 825px; }
  .service-cremation { top: 861px; }
</style>
</head>
<body>
<main class="canvas">
  <section class="banner" aria-label="175th anniversary pole banner">
    <svg class="banner-frame" width="465" height="929" viewBox="0 0 465 929" aria-hidden="true">
      <rect x="9" y="9" width="447" height="911" fill="none" stroke="#ffffff" stroke-width="2"/>
      <rect x="16" y="16" width="433" height="897" fill="none" stroke="#ffffff" stroke-width="1.5"/>
      <path d="M9 9 h32 a32 32 0 0 1 -32 32 z" fill="#ffffff"/>
      <path d="M456 9 h-32 a32 32 0 0 0 32 32 z" fill="#ffffff"/>
      <path d="M9 920 h32 a32 32 0 0 0 -32 -32 z" fill="#ffffff"/>
      <path d="M456 920 h-32 a32 32 0 0 1 32 -32 z" fill="#ffffff"/>
    </svg>

    <p class="text-line intro">our</p>

    <svg class="milestone-ornament" viewBox="0 0 285 218" role="img" aria-label="Ornamental scroll frame around the anniversary number">
      <rect x="0" y="0" width="285" height="218" rx="40" fill="#3b4d8c"/>
    </svg>
    <p class="milestone-number">175</p>
    <p class="text-line milestone-unit">years</p>

    <p class="text-line occasion">anniversary</p>

    <div class="brand-mark" aria-hidden="true"></div>
    <p class="text-line brand-name">Brannock Welde</p>

    <div class="divider"></div>
    <p class="text-line service service-homes">Family Funeral Homes</p>
    <p class="text-line service service-cremation">&amp; Cremation Center</p>
  </section>
</main>
</body>
</html>
```